Harborview Estates Business Card for Apartment Buildings

Create business cards for resident managers who run apartment buildings. The audience is the public who are searching for apartment rentals, and current residents who live at the apartment building. Key design element will be incorporating the company logo, however, the logo cannot dominate. The building name and manager name are more important than the logo. Current business card design leaves little room for copy, so we may need to reduce the size on the current card to allow for more space for copy.

Target Market(s)

Adults 18-65 years of age, who are looking for an apartment rental, plus current residents who live at our apartment buildings.

Industry/Entity Type

Property Management

Contact Information for Business Card

A major design element will be use of the company logo. Important property and manager contact information must be part of the design. The size of the logo will need to be reduced to make room for building and manager contact copy.

Font styles to use
Sans Serif

Colors
3176b5
000000
959595
ffffff

Requirements
Must have
• 1) Incorporate the company logo.
• 2) Use the company colors (dark blue, black/grey, over white).
• 3) FEATURE THE BUILDING NAME
• 4) FEATURE THE MANAGER NAME
• 5) The company name is less important than BUILDING and MANAGER
• 6) Manager contact information
• **SEE ATTACHED CREATIVE BRIEF**
Nice to have
• 1) Back of card logo watermark
• 2) Ability to write notes on back of carfd
Should not have
• Avoid letting the company logo dominate the card, the building name and manager are more important than the company logo.

```html
<!DOCTYPE html>
<html lang="en">
<head>
<meta charset="utf-8">
<title>Harborview Estates Business Card</title>
<link href="https://fonts.googleapis.com/css2?family=Arimo:wght@400;700&display=swap" rel="stylesheet">
<style>
  :root {
    --brand-blue: #3176b5;
    --brand-blue-soft: #a9bde0;
    --ink: #000000;
    --grey: #959595;
    --text-grey: #3a3a3a;
    --paper: #ffffff;
    --backdrop: #e6e7ea;
  }
  * { box-sizing: border-box; margin: 0; padding: 0; }
  html, body {
    width: 1200px; height: 1000px; overflow: hidden;
    background: var(--backdrop);
    font-family: "Arimo", Arial, sans-serif;
  }
  .canvas {
    width: 1200px; height: 1000px;
    display: flex; flex-direction: column;
    align-items: center; justify-content: center; gap: 48px;
  }
  .card {
    position: relative;
    width: 630px; height: 360px;
    background: var(--paper);
    box-shadow: 0 10px 28px rgba(0,0,0,0.18);
    overflow: hidden;
  }

  /* Front */
  .card-front { display: flex; align-items: center; justify-content: center; }
  .front-mark { display: flex; align-items: center; gap: 20px; }
  .front-mark .mark-square {
    width: 70px; height: 70px; background: var(--brand-blue-soft);
  }
  .front-mark .company-name {
    color: var(--brand-blue-soft);
    font-weight: 700; font-size: 40px; letter-spacing: 1px; line-height: 1.05;
  }

  /* Back */
  .card-back .company {
    position: absolute; left: 40px; top: 46px;
    display: flex; align-items: center; gap: 10px;
  }
  .card-back .mark-square { width: 36px; height: 36px; background: var(--brand-blue); }
  .card-back .company-name {
    color: var(--brand-blue); font-weight: 700; font-size: 19px; line-height: 1.1;
  }
  .card-back .divider {
    position: absolute; left: 262px; top: 0; bottom: 26px;
    width: 2px; background: var(--brand-blue);
  }
  .card-back .manager {
    position: absolute; left: 40px; top: 224px;
  }
  .manager-name {
    color: var(--brand-blue); font-weight: 700; font-size: 19px; letter-spacing: 0.3px;
  }
  .manager-title { color: var(--text-grey); font-size: 13px; margin-top: 2px; }
  .contact {
    position: absolute; left: 290px; top: 70px;
    color: var(--text-grey); font-size: 13.5px; line-height: 1.45;
  }
  .contact .address { margin-bottom: 6px; }
  .contact dl { display: grid; grid-template-columns: 52px 1fr; }
  .contact dt { font-weight: 700; color: var(--ink); }
  .card-back .band {
    position: absolute; left: 0; right: 0; bottom: 0; height: 26px;
  }
</style>
</head>
<body>
<main class="canvas">
  <section class="card card-front" aria-label="Card front">
    <div class="front-mark">
      <span class="mark-square"></span>
      <span class="company-name">HARBORVIEW<br>ESTATES</span>
    </div>
  </section>

  <section class="card card-back" aria-label="Card back">
    <div class="company">
      <span class="mark-square"></span>
      <span class="company-name">HARBORVIEW<br>ESTATES</span>
    </div>
    <div class="divider"></div>
    <div class="manager">
      <p class="manager-name">DANIEL WHITAKER</p>
      <p class="manager-title">Property Manager</p>
    </div>
    <div class="contact">
      <p class="address">1280 Alder Crest Road #B210<br>Portland, OR 97205</p>
      <dl>
        <dt>Phone</dt><dd>:- 503-555-0142</dd>
        <dt>Fax</dt><dd>:- 503-555-0187</dd>
        <dt>Email</dt><dd>:- daniel@harborviewestates.us</dd>
        <dt>Web</dt><dd>:- www.harborviewestates.us</dd>
      </dl>
    </div>
    <svg class="band" viewBox="0 0 630 26" preserveAspectRatio="none" aria-hidden="true">
      <polygon points="0,14 630,0 630,26 0,26" fill="var(--brand-blue)"/>
    </svg>
  </section>
</main>
</body>
</html>
```